Stationery Design Project

Minimal Design. Black and White Colours Only.
Need Business Card
With Compliments slip
Letterhead
A4 Folder

Target Market(s)

Luxury architectual designed home owners

Industry/Entity Type

Business

Requirements
Must have
• Black and White colours only. Suggest some good textured stock for business card for future printing. try to use font that is used in my logo our some other minimal modern font.

```html
<!DOCTYPE html>
<html lang="en">
<head>
<meta charset="utf-8">
<title>Varden Estates – Envelope</title>
<link rel="stylesheet" href="https://fonts.googleapis.com/css2?family=Montserrat:wght@500&family=Playfair+Display:ital@1&display=swap">
<style>
  :root {
    --paper: #ffffff;
    --ink: #1e1e1e;
    --band-black: #0d0d0d;
    --band-grey: #979797;
    --window-grey: #a9a9a9;
    --frame-grey: #cfcfcf;
    --silver: #c9c9c9;
    --white: #ffffff;
  }
  * { box-sizing: border-box; margin: 0; padding: 0; }
  html, body {
    width: 1200px;
    height: 1078px;
    overflow: hidden;
    background: var(--paper);
  }
  .canvas {
    position: relative;
    width: 1200px;
    height: 1078px;
  }
  .envelope-face,
  .envelope-back {
    position: absolute;
    left: 1px;
    width: 1198px;
    border: 2px solid var(--frame-grey);
    background: var(--paper);
    overflow: hidden;
  }
  .envelope-face { top: 1px; height: 520px; }
  .envelope-back { top: 556px; height: 521px; }

  .brand {
    position: absolute;
    display: flex;
    align-items: center;
    gap: 22px;
    font-family: "Montserrat", sans-serif;
    font-weight: 500;
    letter-spacing: 0.5px;
    white-space: nowrap;
  }
  .brand-mark {
    width: 46px;
    height: 46px;
  }
  .brand-name { font-size: 27px; }

  .envelope-face .brand { left: 118px; top: 83px; color: var(--ink); }
  .envelope-face .brand-mark { background: var(--ink); }

  .address-window {
    position: absolute;
    left: 112px;
    top: 198px;
    width: 496px;
    height: 146px;
    border: 5px solid var(--window-grey);
    border-radius: 16px;
  }

  .base-band {
    position: absolute;
    left: 0;
    top: 405px;
    width: 1198px;
    height: 80px;
  }
  .web-address {
    position: absolute;
    left: 846px;
    top: 432px;
    display: flex;
    align-items: center;
    gap: 8px;
    color: var(--white);
    font-family: "Playfair Display", serif;
    font-style: italic;
    font-size: 14px;
  }
  .web-address svg { width: 26px; height: 26px; }

  .flap {
    position: absolute;
    left: 0;
    top: 0;
    width: 1198px;
    height: 220px;
  }
  .envelope-back .brand { left: 430px; top: 84px; color: var(--silver); }
  .envelope-back .brand-mark {
    width: 44px;
    height: 44px;
    border-radius: 50%;
    background: var(--silver);
  }
</style>
</head>
<body>
<main class="canvas">

  <section class="envelope-face" aria-label="Envelope front">
    <div class="brand">
      <span class="brand-mark"></span>
      <span class="brand-name">VARDEN ESTATES</span>
    </div>

    <div class="address-window"></div>

    <svg class="base-band" viewBox="0 0 1198 80" preserveAspectRatio="none" aria-hidden="true">
      <defs>
        <linearGradient id="band-shade" x1="0" y1="0" x2="1" y2="1">
          <stop offset="0" stop-color="#060606"/>
          <stop offset="0.5" stop-color="#1a1a1a"/>
          <stop offset="1" stop-color="#080808"/>
        </linearGradient>
      </defs>
      <path d="M0 25 H735 C770 25 775 12 800 12 L800 48 H0 Z" fill="var(--band-grey)"/>
      <path d="M0 50 H740 C790 50 800 5 860 5 H1198 V78 H0 Z" fill="url(#band-shade)"/>
    </svg>

    <div class="web-address">
      <svg viewBox="0 0 26 26" aria-hidden="true">
        <circle cx="13" cy="13" r="11" fill="none" stroke="#fff" stroke-width="1.2"/>
        <ellipse cx="13" cy="13" rx="5" ry="11" fill="none" stroke="#fff" stroke-width="1"/>
        <line x1="2" y1="13" x2="24" y2="13" stroke="#fff" stroke-width="1"/>
        <line x1="4" y1="7" x2="22" y2="7" stroke="#fff" stroke-width="1"/>
        <line x1="4" y1="19" x2="22" y2="19" stroke="#fff" stroke-width="1"/>
      </svg>
      <span>www.vardenestates.com</span>
    </div>
  </section>

  <section class="envelope-back" aria-label="Envelope back">
    <svg class="flap" viewBox="0 0 1198 220" aria-hidden="true">
      <defs>
        <linearGradient id="flap-shade" x1="0" y1="0" x2="1" y2="1">
          <stop offset="0" stop-color="#050505"/>
          <stop offset="0.45" stop-color="#1c1c1c"/>
          <stop offset="1" stop-color="#070707"/>
        </linearGradient>
      </defs>
      <path d="M3 2 H1196 L1166 86 L716 212 H481 L22 92 Z" fill="url(#flap-shade)"/>
    </svg>
    <div class="brand">
      <span class="brand-mark"></span>
      <span class="brand-name">VARDEN ESTATES</span>
    </div>
  </section>

</main>
</body>
</html>
```